Heron Property Inspection business card

I am the principal inspector of Heron Property Inspections. I serve Northern Virginia from Winchester to Arlington.Associate, Federated Guild of Dwelling Examiners (FGDE)Graduate, FGDE Home Inspectors CourseNational Association of Home Inspectors ExamI'd like the business card to look more professional than comical.I pulled the attached picture off the web. I'd like to have something like that or an image of a house as my logo on the cards.

Target Market(s)

Persons who recently purchased a home.

Industry/Entity Type

Business

Contact Information for Business Card

Bob AllenBadger Home Inspections, LLC.4455 River RoadBluemont, Virginia 20135cell: 703-231-6680e-mail: tkmarlow@postvale.net

Font styles to use
Serif
Sans Serif

Requirements
Must have
• I'd like to have a logo, something that identifies me as a home inspector. The attached images are something that I'd like to have incorporated into my business card logo.
Nice to have
• I'd like a sketch of a house and/or a magnifying glass showing a house being inspected. The attached images are used as a suggestion only, I do not own the images.
Should not have
• Gimmicky stuff. I want to appear professional and trustworthy.

```html
<!DOCTYPE html>
<html lang="en">
<head>
<meta charset="utf-8">
<title>Heron Property Inspections – Business Card</title>
<link rel="stylesheet" href="https://fonts.googleapis.com/css2?family=Open+Sans:wght@400;600&display=swap">
<style>
  :root {
    --page-bg: #e9e7e3;
    --card-white: #ffffff;
    --card-shade: #f1f1f1;
    --ink: #333436;
    --ink-soft: #5a5b5e;
    --brand-red: #a11d22;
    --band-dark: #3b3c3f;
    --band-line: #ffffff;
  }
  * { margin: 0; padding: 0; box-sizing: border-box; }
  html, body {
    width: 1200px;
    height: 892px;
    overflow: hidden;
    background: var(--page-bg);
    font-family: "Open Sans", Arial, sans-serif;
  }
  .business-card {
    position: absolute;
    left: 100px;
    top: 160px;
    width: 1000px;
    height: 572px;
    border-radius: 36px;
    overflow: hidden;
    background: linear-gradient(180deg, var(--card-white) 0%, var(--card-white) 55%, var(--card-shade) 100%);
    box-shadow: 0 10px 30px rgba(0, 0, 0, 0.18);
    color: var(--ink);
    text-align: center;
  }
  .brand-lockup {
    position: absolute;
    top: 52px;
    left: 0;
    right: 0;
    display: flex;
    justify-content: center;
    align-items: center;
    gap: 22px;
  }
  .brand-name {
    font-weight: 600;
    color: var(--ink);
    line-height: 1.15;
    text-align: left;
  }
  .brand-name .principal {
    display: block;
    font-size: 40px;
  }
  .brand-name .firm {
    display: block;
    font-size: 30px;
  }
  .brand-mark {
    width: 78px;
    height: 78px;
    background: var(--brand-red);
    flex: none;
  }
  .employee-name {
    position: absolute;
    top: 196px;
    left: 0;
    right: 0;
    font-size: 60px;
    font-weight: 400;
    color: var(--brand-red);
    line-height: 1;
  }
  .employee-title {
    position: absolute;
    top: 270px;
    left: 0;
    right: 0;
    font-size: 22px;
    color: var(--ink-soft);
  }
  .contact-list {
    position: absolute;
    top: 322px;
    left: 0;
    right: 0;
    list-style: none;
    font-size: 28px;
    line-height: 44px;
    color: var(--ink);
  }
  .address-band {
    position: absolute;
    left: 0;
    right: 0;
    bottom: 0;
    height: 124px;
    background: var(--band-dark);
  }
  .address-band::before {
    content: "";
    position: absolute;
    left: 0;
    right: 0;
    top: 12px;
    height: 3px;
    background: var(--band-line);
  }
  .address-band .address {
    position: absolute;
    left: 0;
    right: 0;
    top: 44px;
    font-size: 32px;
    color: var(--band-line);
  }
</style>
</head>
<body>
  <article class="business-card">
    <header class="brand-lockup">
      <h1 class="brand-name">
        <span class="principal">Tim Marlow</span>
        <span class="firm">Heron Property Inspections, LLC</span>
      </h1>
      <div class="brand-mark" role="img" aria-label="Company house logo mark"></div>
    </header>
    <p class="employee-name">Employee name</p>
    <p class="employee-title">Managing Director</p>
    <ul class="contact-list">
      <li class="phone">703-555-0192</li>
      <li class="email">tkmarlow@postvale.net</li>
    </ul>
    <footer class="address-band">
      <p class="address">7182 Quarry Lane Fernhill, Virginia 20148</p>
    </footer>
  </article>
</body>
</html>
```